Hartwell Estates Business Cards

I would like a business card that includes myself and my partner.
Includes: Logo, office #, email, website, our names, our numbers and possibly the address. I would also like the logo to be embossed and the card to be horizontal.
There is a photo of our yard signs to give you an idea of the colors of our business.

Target Market(s)

Everyone in real estate market.
We are in a rural area. Our clientele are from all socioeconomic backgrounds.

Industry/Entity Type

Real Estate Agent

Contact Information for Business Card

Company Name: Hartwell Estates
Our Names, Titles & Cell #'s : Dana Pembrook-Broker (555).317.6624, Marla Pembrook-Realtor (555).609.1385
Office #: (555).240.3918
Website: hartwellestates-demo.com
Joint Email: pembrook@hartwellestates-demo.com
Office Address: 418B W. Calloway Ave.
Fernwood, LA. 70913

Font styles to use
Serif

Requirements
Must have
• HORIZONTAL, Logo, Myself and my partners names, Our cell #'s, our office #, our website, our email address
Nice to have
• Embossed logo, office address, our titles.

```html
<!DOCTYPE html>
<html lang="en">
<head>
<meta charset="utf-8">
<title>Hartwell Estates – Business Card</title>
<link rel="stylesheet" href="https://fonts.googleapis.com/css2?family=Libre+Baskerville:wght@400;700&display=swap">
<style>
  :root {
    --ink: #48215f;
    --ink-deep: #3d1a53;
    --paper: #ffffff;
    --skyline-top: #efe8f4;
    --skyline-bottom: #ffffff;
    --serif: "Libre Baskerville", Georgia, serif;
  }
  * { margin: 0; padding: 0; box-sizing: border-box; }
  html, body { width: 1200px; height: 720px; overflow: hidden; background: var(--paper); }
  .card {
    position: relative;
    width: 1200px;
    height: 720px;
    background: var(--paper);
    font-family: var(--serif);
    color: var(--ink);
  }
  .skyline {
    position: absolute;
    left: 0; top: 55px;
    width: 1200px; height: 132px;
    background: linear-gradient(to bottom, var(--skyline-top), var(--skyline-bottom));
  }
  .edge-left {
    position: absolute;
    left: 0; top: 92px;
    width: 2px; height: 553px;
    background: var(--ink);
  }
  .edge-right {
    position: absolute;
    right: 0; top: 176px;
    width: 2px; height: 469px;
    background: var(--ink);
  }
  .footer-rule {
    position: absolute;
    left: 0; top: 643px;
    width: 1200px; height: 3px;
    background: var(--ink-deep);
  }
  .footer-band {
    position: absolute;
    left: 0; top: 659px;
    width: 1200px; height: 61px;
    background: var(--ink-deep);
  }
  .brand {
    position: absolute;
    left: 88px; top: 242px;
    display: flex;
    align-items: center;
    gap: 26px;
  }
  .brand-mark {
    width: 118px; height: 118px;
    border-radius: 50%;
    background: var(--ink);
  }
  .brand-name {
    font-size: 46px;
    font-weight: 700;
    line-height: 1.15;
    color: var(--ink);
  }
  .contact-list {
    position: absolute;
    left: 115px; top: 406px;
    list-style: none;
  }
  .contact-item {
    display: flex;
    align-items: flex-start;
    gap: 22px;
    height: 46px;
    font-size: 19.5px;
    font-weight: 700;
    line-height: 38px;
  }
  .contact-item.address { line-height: 37px; }
  .contact-icon {
    flex: none;
    width: 38px; height: 38px;
  }
  .partner {
    position: absolute;
    right: 98px;
    width: 480px;
    text-align: right;
  }
  .partner.broker { top: 318px; }
  .partner.realtor { top: 498px; }
  .partner-name {
    font-size: 32px;
    font-weight: 700;
    letter-spacing: 0.5px;
    line-height: 36px;
  }
  .partner-title {
    font-size: 22px;
    font-weight: 400;
    line-height: 30px;
    margin-top: 2px;
  }
  .partner-phone {
    font-size: 26px;
    font-weight: 400;
    line-height: 32px;
  }
  .partner-divider {
    position: absolute;
    right: 98px; top: 468px;
    width: 262px;
    height: 1.5px;
    background: var(--ink);
    border: 0;
  }
</style>
</head>
<body>
<main class="card">
  <div class="skyline" role="img" aria-label="Outlined city skyline running across the top of the card"></div>
  <div class="edge-left"></div>
  <div class="edge-right"></div>

  <div class="brand">
    <div class="brand-mark" aria-hidden="true"></div>
    <div class="brand-name">Hartwell<br>Estates</div>
  </div>

  <ul class="contact-list">
    <li class="contact-item">
      <svg class="contact-icon" viewBox="0 0 38 38" aria-hidden="true">
        <circle cx="19" cy="19" r="19" fill="var(--ink)"/>
        <rect x="12" y="10" width="14" height="18" rx="3" fill="none" stroke="#fff" stroke-width="1.8"/>
        <path d="M15.5 14c0 5 3 8.5 7 9.5l1.5-2-2.5-1.5-1 1c-1.5-.8-2.6-2-3.2-3.5l1-1-1-2.6z" fill="#fff"/>
      </svg>
      <span>(555).240.3918</span>
    </li>
    <li class="contact-item">
      <svg class="contact-icon" viewBox="0 0 38 38" aria-hidden="true">
        <circle cx="19" cy="19" r="19" fill="var(--ink)"/>
        <g fill="none" stroke="#fff" stroke-width="1.5">
          <circle cx="19" cy="19" r="9"/>
          <ellipse cx="19" cy="19" rx="4" ry="9"/>
          <line x1="10" y1="19" x2="28" y2="19"/>
          <line x1="11.5" y1="14.5" x2="26.5" y2="14.5"/>
          <line x1="11.5" y1="23.5" x2="26.5" y2="23.5"/>
        </g>
      </svg>
      <span>hartwellestates-demo.com</span>
    </li>
    <li class="contact-item">
      <svg class="contact-icon" viewBox="0 0 38 38" aria-hidden="true">
        <circle cx="19" cy="19" r="19" fill="var(--ink)"/>
        <rect x="10" y="13" width="18" height="13" rx="1.5" fill="#fff"/>
        <path d="M10.5 13.5l8.5 7 8.5-7" fill="none" stroke="var(--ink)" stroke-width="1.5"/>
      </svg>
      <span>pembrook@hartwellestates-demo.com</span>
    </li>
    <li class="contact-item address">
      <svg class="contact-icon" viewBox="0 0 38 38" aria-hidden="true">
        <circle cx="19" cy="19" r="19" fill="var(--ink)"/>
        <path d="M19 28s-6-6.5-6-11a6 6 0 0 1 12 0c0 4.5-6 11-6 11z" fill="none" stroke="#fff" stroke-width="1.8"/>
        <circle cx="19" cy="17" r="2.2" fill="#fff"/>
      </svg>
      <span>418B W. Calloway Ave.<br>Fernwood, LA. 70913</span>
    </li>
  </ul>

  <section class="partner broker">
    <p class="partner-name">DANA PEMBROOK</p>
    <p class="partner-title">Broker</p>
    <p class="partner-phone">(555).317.6624</p>
  </section>
  <hr class="partner-divider">
  <section class="partner realtor">
    <p class="partner-name">MARLA PEMBROOK</p>
    <p class="partner-title">Realtor</p>
    <p class="partner-phone">(555).609.1385</p>
  </section>

  <div class="footer-rule"></div>
  <div class="footer-band"></div>
</main>
</body>
</html>
```